We need a .psd design for a store we are creating called Brisk Purses. I will need only the main home page designed.

The store will be an eCommerce website that sells custom printed men's wallets. Customers will come onto the website and be able to upload their own images or add text to the front, back and inside of the wallet. We will initially be launching with one wallet style and will be expanding our range in the future for now the only images of a wallet on the website should be of the style attached.

There will be multiple templates that a customer can choose and edit the design of so there will effectively be a large number of products on display in the store. However, on the homepage there should just be a couple of featured products and the main emphasis should be on the features of the wallet/website and links to other areas of the website (customise your own wallet, edit our templates, bespoke designer wallets).

For the styling of the website, it needs to be funky and fresh with lots of colour. The logo of the website is attached and the styling should mirror the logo style.

The main features of the website should be on the home page. These features are:
- 5 year money back guarantee on wallet
- High quality, durable leather, made to last
- customer can upload photo and edit them online with our online picture editor
- 3d mockup of the wallet as you are designing it to show what it looks like with custom images on
- Edit any of our ready made wallet designs

Features of this wallet may be used as well - these can be viewed on "Image 6" of the attached product image .psd files.

Attached are the logo for the website and the wallet product photos. The product photos are provided in .psd format and have smart objects so that you can add any image to the front/inside of the wallets for any images on the website you create. Fee free to edit them and use them for banner images and feature images however you feel necessary.

The term "what does you wallet say about you" should be used as this is a tagline for most of the marketing - based on the fact that the wallets are personalised to each individual they will show off that individuals personality and what they like.

The eventual website will be hosted on cartnest and will more than likely use the "TillBay" theme. This is a highly adaptable theme and examples of the layout styles for the homepage can be found here: http://harbor.quillpages.example/cartnest/tillbay-intro/?storefront=loom-assets however i do not want you to just copy a ready made template and stick some stock photos in - I only want one page designing here, put the effort in with the banners and feature images and you'll win this.

Any images that you create for hero sliders/banners should be provided in .psd format so that they can be edited as necessary in the future. A newsletter popup should also be designed as the website will have postwren integration, the newsletter popup is a 500 x 750 image that pops up with a message saying "subscribe to our newsletter and get 10% off your next order".

There should also be an area of the page that has customer testimonials.

Target Market(s)

Males, aged 18 - 45

Industry/Entity Type

Retail

Number of Pages Required

1 page

Font styles to use
Serif
Decorative
Script

Colors

Designer to choose colors to be used in the design.

Requirements
Must have
• Vibrant and uplifting feel to the website
• Design which reflects the logo
• Features of the website and wallets should feature prominently on the homepage (but not in banner/hero image)
Nice to have
• hipster/geek/easygoing vibe
• Images that have used the wallet .psd files and have different designs on them showing customers that anything can be printed on the wallets
• Custom images/styles for the featured images and main banner.
Should not have
• - Boring images
• - Stock Photos
• - Mundane feel
• - Square block style images - try putting images in circles or geometric shapes with colours, just adding a stock photo to some "lorem Ipsum" text will not win you this contest

```html
<!DOCTYPE html>
<html lang="en">
<head>
<meta charset="utf-8">
<title>Brisk Purses – Custom Printed Wallets</title>
<link rel="stylesheet" href="https://fonts.googleapis.com/css2?family=Fredoka:wght@600;700&family=Montserrat:wght@500;700;800&family=Arimo:ital,wght@0,700;1,400&display=swap">
<style>
  :root {
    --ink: #1b1f27;
    --green: #12b25e;
    --yellow: #f7e51b;
    --blue: #1aa0e0;
    --red: #f0473c;
    --pink: #ec3d97;
    --nav-active: #e8352b;
    --mist: #f4f4f6;
    --card: #f3f3f5;
    --band-grey: #f1f1f3;
    --body-grey: #3d3f45;
  }
  * { box-sizing: border-box; margin: 0; padding: 0; }
  html, body { width: 1200px; height: 2324px; overflow: hidden; background: #fff; }
  body { font-family: "Montserrat", sans-serif; color: var(--ink); }
  a { color: inherit; text-decoration: none; }
  .page { position: relative; width: 1200px; height: 2324px; overflow: hidden; }
  .abs { position: absolute; }

  /* Header */
  .brand { left: 106px; top: 28px; display: flex; align-items: center; gap: 14px; }
  .brand-dot { width: 52px; height: 52px; border-radius: 50%; background: var(--ink); }
  .brand-name { font-weight: 800; font-size: 30px; color: var(--ink); letter-spacing: -0.5px; }
  .main-nav { top: 46px; right: 104px; display: flex; gap: 20px; font-size: 12.5px; font-weight: 700; white-space: nowrap; }
  .main-nav a.is-active { color: var(--nav-active); }

  /* Hero */
  .hero-title { left: 0; width: 1172px; top: 122px; text-align: center; font-family: "Fredoka", sans-serif; font-weight: 700; font-size: 48px; line-height: 48px; color: var(--ink); }
  .hero-title span { display: block; }
  .hero-art { left: 0; top: 0; }
  .polaroid { left: 140px; top: 252px; width: 186px; height: 212px; background: #fff; transform: rotate(-5deg); box-shadow: 0 4px 14px rgba(0,0,0,.25); padding: 12px 12px 36px; }
  .polaroid .photo { width: 100%; height: 100%; background: linear-gradient(160deg, #b9a79b, #7b6358 60%, #d7cdc6); }
  .wallet-open { left: 376px; top: 237px; width: 456px; height: 318px; border-radius: 10px; background: linear-gradient(90deg, #f5e21c 0%, #3fb1df 35%, #f25b92 60%, #e94a3b 85%, #f5e21c 100%); box-shadow: 0 6px 16px rgba(0,0,0,.3); border: 6px solid #2a2a2a; }
  .wallet-flap { left: 422px; top: 330px; width: 266px; height: 250px; border-radius: 14px; background: linear-gradient(165deg, #e2dcd6, #a48a7c 55%, #6d5549); box-shadow: 0 8px 18px rgba(0,0,0,.35); border: 5px solid #2a2a2a; }
  .phone { left: 875px; top: 200px; width: 145px; height: 295px; border-radius: 22px; background: #f2f2f2; border: 2px solid #b8b8b8; box-shadow: 0 3px 8px rgba(0,0,0,.2); }
  .phone-screen { position: absolute; left: 9px; top: 38px; right: 9px; bottom: 38px; background: linear-gradient(135deg, var(--pink), var(--yellow) 40%, var(--blue) 65%, var(--red)); }
  .phone-ear { position: absolute; top: 16px; left: 52px; width: 38px; height: 5px; border-radius: 3px; background: #bbb; }
  .phone-home { position: absolute; bottom: 8px; left: 58px; width: 25px; height: 25px; border-radius: 50%; border: 2px solid #bbb; }

  /* Call-to-action buttons */
  .cta { top: 622px; width: 277px; height: 66px; background: var(--ink); color: var(--yellow); font-weight: 800; font-size: 18px; line-height: 21px; text-align: center; display: flex; align-items: center; justify-content: center; overflow: hidden; }
  .cta-splash { position: absolute; right: -14px; top: -12px; width: 58px; height: 58px; border-radius: 50%; }
  .cta-label { position: relative; }

  /* Feature list */
  .feature { top: 734px; width: 230px; }
  .feature-icon { position: relative; width: 100px; height: 94px; }
  .feature-blob { position: absolute; left: 8px; top: 0; width: 86px; height: 92px; border-radius: 48% 52% 44% 56%; }
  .feature-icon svg { position: absolute; left: 18px; top: 14px; }
  .feature-text { margin-top: 6px; font-size: 15.5px; line-height: 19.5px; font-weight: 500; text-transform: uppercase; letter-spacing: -0.2px; }
  .feature-text b { font-weight: 800; }

  /* Featured products */
  .section-title { left: 0; width: 1196px; text-align: center; font-weight: 800; font-size: 20px; }
  .product-card { top: 992px; width: 300px; height: 219px; background: var(--card); }

  /* Wallet anatomy diagram */
  .anatomy-lines { left: 0; top: 1280px; }
  .anatomy-wallet { left: 523px; top: 1375px; width: 152px; height: 148px; border-radius: 6px; background: linear-gradient(135deg, var(--yellow) 0%, var(--blue) 35%, var(--pink) 62%, var(--red) 85%, var(--green)); border: 3px solid #2a2a2a; }
  .anatomy-spot { width: 110px; height: 110px; border-radius: 50%; display: flex; align-items: center; justify-content: center; }
  .anatomy-spot .inner { width: 76px; height: 76px; border-radius: 50%; background: #3a3533; }

  /* Testimonials */
  .testimonials { left: 0; top: 1653px; width: 1188px; height: 485px; background: var(--mist); }
  .swirl { border-radius: 46% 54% 40% 60%; }
  .swirl-right { left: 969px; top: 1586px; width: 219px; height: 414px; background: linear-gradient(160deg, var(--blue), var(--yellow) 30%, var(--red) 55%, #b9b9b9 75%, var(--green)); }
  .swirl-left { left: -20px; top: 1742px; width: 239px; height: 422px; background: linear-gradient(200deg, var(--yellow), #c9c9c9 30%, var(--green) 50%, var(--red) 75%, var(--blue)); }
  .quote { left: 286px; width: 600px; font-family: "Arimo", sans-serif; color: var(--body-grey); }
  .quote-name { font-weight: 700; font-size: 17px; line-height: 20px; }
  .quote-text { font-style: italic; font-size: 15.5px; line-height: 19px; }
  .chevron { left: 580px; top: 2094px; }

  /* Footer */
  .footer-nav { left: 0; width: 1188px; top: 2194px; display: flex; justify-content: center; align-items: center; gap: 18px; font-size: 11.5px; font-weight: 800; white-space: nowrap; }
  .social-group { display: flex; gap: 17px; margin-left: 6px; }
  .social { display: block; width: 15px; height: 15px; background: var(--ink); border-radius: 2px; }
  .legal { left: 0; width: 1188px; top: 2237px; text-align: center; font-size: 10.5px; font-weight: 500; }
  .legal u { text-decoration: underline; }
</style>
</head>
<body>
<div class="page">

  <!-- Header -->
  <div class="abs brand">
    <div class="brand-dot"></div>
    <div class="brand-name">Brisk Purses</div>
  </div>
  <nav class="abs main-nav">
    <a class="is-active">HOME</a>
    <a>ABOUT US</a>
    <a>BROWSE OUR DESIGNS</a>
    <a>SIGN IN</a>
    <a>CONTACT US</a>
  </nav>

  <!-- Hero background shapes -->
  <svg class="abs hero-art" width="1200" height="620" viewBox="0 0 1200 620">
    <polygon points="0,153 480,262 420,440 138,588 138,430 0,297" fill="var(--green)"/>
    <polygon points="828,344 1188,273 1188,414 828,575" fill="var(--band-grey)"/>
    <path d="M868 188 C 850 160, 830 155, 806 170" fill="none" stroke="var(--ink)" stroke-width="4" stroke-linecap="round"/>
    <path d="M806 170 l 14 -10 M806 170 l 16 4" fill="none" stroke="var(--ink)" stroke-width="4" stroke-linecap="round"/>
    <path d="M312 478 C 320 505, 345 515, 382 512" fill="none" stroke="var(--ink)" stroke-width="4" stroke-linecap="round"/>
    <path d="M382 512 l -14 -10 M382 512 l -13 10" fill="none" stroke="var(--ink)" stroke-width="4" stroke-linecap="round"/>
  </svg>

  <h1 class="abs hero-title"><span>funk up</span><span>your wallet.</span></h1>

  <div class="abs polaroid"><div class="photo" role="img" aria-label="Instant photo of a smiling family"></div></div>
  <div class="abs wallet-open" role="img" aria-label="Open wallet printed with bright paint splashes"></div>
  <div class="abs wallet-flap" role="img" aria-label="Wallet front printed with the family photo"></div>
  <div class="abs phone" role="img" aria-label="Phone showing a paint splash wallet design">
    <div class="phone-ear"></div><div class="phone-screen"></div><div class="phone-home"></div>
  </div>

  <!-- Calls to action -->
  <a class="abs cta" style="left:137px"><span class="cta-splash" style="background:var(--blue)"></span><span class="cta-label">CUSTOMISE<br>YOUR OWN WALLET</span></a>
  <a class="abs cta" style="left:455px"><span class="cta-splash" style="background:var(--green)"></span><span class="cta-label">EDIT<br>OUR TEMPLATES</span></a>
  <a class="abs cta" style="left:772px"><span class="cta-splash" style="background:var(--red)"></span><span class="cta-label">BESPOKE<br>DESIGNER WALLETS</span></a>

  <!-- Features -->
  <div class="abs feature" style="left:106px">
    <div class="feature-icon"><div class="feature-blob" style="background:var(--green)"></div>
      <svg width="66" height="70" viewBox="0 0 66 70"><path d="M20 30 V20 a13 13 0 0 1 26 0 V30" fill="none" stroke="var(--ink)" stroke-width="5"/><rect x="12" y="30" width="42" height="36" fill="#fff" stroke="var(--ink)" stroke-width="5"/><text x="33" y="58" text-anchor="middle" font-family="Montserrat, sans-serif" font-weight="800" font-size="22" fill="var(--ink)">5</text></svg>
    </div>
    <p class="feature-text"><b>5 year money-<br>back</b> guarantee<br>on wallet</p>
  </div>
  <div class="abs feature" style="left:289px">
    <div class="feature-icon"><div class="feature-blob" style="background:var(--yellow)"></div>
      <svg width="66" height="70" viewBox="0 0 66 70"><path d="M33 6 l7 6 9-1 2 9 8 5-4 8 4 8-8 5-2 9-9-1-7 6-7-6-9 1-2-9-8-5 4-8-4-8 8-5 2-9 9 1z" fill="#fff" stroke="var(--ink)" stroke-width="4"/><circle cx="33" cy="35" r="14" fill="none" stroke="var(--ink)" stroke-width="4"/><path d="M26 35 l5 5 9-10" fill="none" stroke="var(--ink)" stroke-width="4"/></svg>
    </div>
    <p class="feature-text"><b>High quality,</b><br>durable leather,<br>made to last</p>
  </div>
  <div class="abs feature" style="left:473px">
    <div class="feature-icon"><div class="feature-blob" style="background:var(--blue)"></div>
      <svg width="70" height="70" viewBox="0 0 70 70"><ellipse cx="35" cy="38" rx="32" ry="14" fill="none" stroke="var(--ink)" stroke-width="4"/><rect x="16" y="18" width="38" height="36" fill="#fff" stroke="var(--ink)" stroke-width="4"/><path d="M24 36 h18 m-7 -7 l7 7 -7 7" fill="none" stroke="var(--ink)" stroke-width="4"/></svg>
    </div>
    <p class="feature-text"><b>3D mockup</b><br>of the wallet as<br>you are designing</p>
  </div>
  <div class="abs feature" style="left:678px">
    <div class="feature-icon"><div class="feature-blob" style="background:var(--red)"></div>
      <svg width="72" height="70" viewBox="0 0 72 70"><path d="M6 22 h44 v30 h-44z" fill="#fff" stroke="var(--ink)" stroke-width="4"/><path d="M6 22 l6-10 h32 l6 10" fill="none" stroke="var(--ink)" stroke-width="4"/><path d="M18 52 v-14 h12 v14" fill="none" stroke="var(--ink)" stroke-width="4"/><path d="M46 34 l20 8 -8 3 6 10 -5 3 -6-10 -6 6z" fill="#fff" stroke="var(--ink)" stroke-width="3.5" stroke-linejoin="round"/></svg>
    </div>
    <p class="feature-text"><b>Edit</b> any of our<br>ready made<br>wallet designs</p>
  </div>
  <div class="abs feature" style="left:856px; width:300px">
    <div class="feature-icon"><div class="feature-blob" style="background:var(--pink)"></div>
      <svg width="90" height="70" viewBox="0 0 90 70"><rect x="22" y="6" width="60" height="40" fill="#fff" stroke="var(--ink)" stroke-width="4"/><rect x="4" y="26" width="32" height="36" fill="#fff" stroke="var(--ink)" stroke-width="4"/><circle cx="20" cy="40" r="5" fill="var(--ink)"/><path d="M11 56 a9 8 0 0 1 18 0" fill="var(--ink)"/><path d="M44 34 l14 -14 m-10 0 h10 v10" fill="none" stroke="var(--ink)" stroke-width="4"/></svg>
    </div>
    <p class="feature-text"><b>Upload your photo</b><br>and edit them online with<br>our online picture editor</p>
  </div>

  <!-- Featured products -->
  <h2 class="abs section-title" style="top:942px">FEATURED PRODUCTS</h2>
  <div class="abs product-card" style="left:108px"></div>
  <div class="abs product-card" style="left:445px"></div>
  <div class="abs product-card" style="left:784px"></div>

  <!-- Wallet anatomy -->
  <svg class="abs anatomy-lines" width="1200" height="320" viewBox="0 0 1200 320">
    <g fill="none" stroke="var(--ink)" stroke-width="2">
      <polyline points="390,53 495,53 523,110"/>
      <polyline points="335,161 523,161"/>
      <polyline points="390,275 495,275 523,223"/>
      <polyline points="790,53 703,53 675,110"/>
      <polyline points="860,161 675,161"/>
      <polyline points="790,275 703,275 675,223"/>
    </g>
  </svg>
  <div class="abs anatomy-wallet" role="img" aria-label="Closed wallet printed with paint splashes"></div>
  <div class="abs anatomy-spot" style="left:281px; top:1273px; background:var(--blue)" role="img" aria-label="Close-up of reinforced corners"><div class="inner"></div></div>
  <div class="abs anatomy-spot" style="left:226px; top:1386px; background:var(--red)" role="img" aria-label="Close-up of the slim wallet profile"><div class="inner"></div></div>
  <div class="abs anatomy-spot" style="left:281px; top:1500px; background:var(--green)" role="img" aria-label="Close-up of the coin compartment"><div class="inner"></div></div>
  <div class="abs anatomy-spot" style="left:789px; top:1270px; background:var(--yellow)" role="img" aria-label="Close-up of durable luxury leather"><div class="inner"></div></div>
  <div class="abs anatomy-spot" style="left:859px; top:1386px; background:#111" role="img" aria-label="Close-up of the credit card slots"><div class="inner" style="background:#5a4a44"></div></div>
  <div class="abs anatomy-spot" style="left:789px; top:1500px; background:var(--pink)" role="img" aria-label="Close-up of the two note pockets"><div class="inner"></div></div>

  <!-- Testimonials -->
  <section class="abs testimonials"></section>
  <div class="abs swirl swirl-right" role="img" aria-label="Colourful swirling wave pattern"></div>
  <div class="abs swirl swirl-left" role="img" aria-label="Colourful swirling wave pattern"></div>
  <h2 class="abs section-title" style="top:1692px">WHAT THEY SAY ABOUT US</h2>
  <div class="abs quote" style="top:1740px">
    <p class="quote-name">Lorem Ipsum Dolor</p>
    <p class="quote-text">sit amet, consectetur adipiscing elit, sed do eiusmod tempor incididunt ut labore et dolore magna aliqua. Ut enim ad minim veniam, quis nostrud exercitation ullamco laboris nisi ut aliquip ex ea commodo consequat.</p>
  </div>
  <div class="abs quote" style="top:1860px">
    <p class="quote-name">Lorem Ipsum Dolor</p>
    <p class="quote-text">sit amet, consectetur adipiscing elit, sed do eiusmod tempor incididunt ut labore et dolore magna aliqua. Ut enim ad minim veniam, quis nostrud exercitation ullamco laboris nisi ut aliquip ex ea commodo consequat.</p>
  </div>
  <div class="abs quote" style="top:1978px">
    <p class="quote-name">Lorem Ipsum Dolor</p>
    <p class="quote-text">sit amet, consectetur adipiscing elit, sed do eiusmod tempor incididunt ut labore et dolore magna aliqua. Ut enim ad minim veniam, quis nostrud exercitation ullamco laboris nisi ut aliquip ex ea commodo consequat.</p>
  </div>
  <svg class="abs chevron" width="26" height="16" viewBox="0 0 26 16"><polyline points="2,3 13,13 24,3" fill="none" stroke="var(--ink)" stroke-width="2"/></svg>

  <!-- Footer -->
  <nav class="abs footer-nav">
    <a>HOME</a>
    <a>ABOUT US</a>
    <a>BROWSE OUR DESIGNS</a>
    <a>SIGN IN</a>
    <a>CONTACT US</a>
    <span class="social-group">
      <span class="social"></span>
      <span class="social"></span>
      <span class="social"></span>
    </span>
  </nav>
  <p class="abs legal"><u>Terms of Use</u> &nbsp;&amp;&nbsp; <u>Privacy Policy</u> &nbsp;© 2018 Brisk Purses • All rights reserved</p>

</div>
</body>
</html>
```